Fresh and unique Mortgage Broking business needs website design.

We need a professional yet fresh, bright and colourful website for my Mortgage broking business.
We specialise in the Non conforming/sub prime market with clients who have been rejected by other banks or have trouble getting finance through a traditional lender.
We are called Lark Lending and we aim to provide Hope to our clients when they have thought there was no hope.
I would like it to be on a Wordpress platform as I plan to do a lot of postings, both written and video and I need it to be easy to use.
I would also like it to be able to have a clear and simple enquiry box on the first page to capture contact details and notify me via email.

I have already had the logo designed in both green and black and a white version.
I have also had a a header made up using the white logo with leaves background that could possibly be used as the website header which I have used as my facebook header.

https://www.pagebook-example.com/MarcusDellowLark/

I tried playing around with a sitebuild website builder which kind of got some of the brightness and colours I was after but it had a lot to go.

http://larklending.sitebuildexample.com/

Industry/Entity Type

Finance

Number of Pages Required

4 page

Colors
0292cd
00a990
fbed22
ffc214
f78f20
ec1f27

Requirements
Nice to have
• I'm not sure what the difference between uncoded and coded website is so I'm not sure what I need?

```html
<!DOCTYPE html>
<html lang="en">
<head>
<meta charset="utf-8">
<title>Lark Lending</title>
<link rel="stylesheet" href="https://fonts.googleapis.com/css2?family=Open+Sans:wght@400;600;700;800&display=swap">
<style>
:root{
  --blue:#0a8ccc;
  --teal:#00a990;
  --orange:#f7941d;
  --red:#ec1f27;
  --brand-green:#1b7a3e;
  --text:#6b6b6b;
  --dark:#444444;
  --band:#f4f4f4;
  --white:#ffffff;
}
*{box-sizing:border-box;margin:0;padding:0}
html,body{width:742px;height:1200px;overflow:hidden}
body{position:relative;background:var(--white);font-family:"Open Sans",Arial,sans-serif;color:var(--text)}
.site-header{position:absolute;left:0;top:0;width:742px;height:62px;background:var(--white)}
.brand{position:absolute;left:46px;top:20px;font-size:20px;font-weight:700;color:var(--brand-green);letter-spacing:.2px}
.main-nav{position:absolute;right:46px;top:23px;display:flex;align-items:center}
.main-nav a{font-size:7.5px;font-weight:700;color:#555;text-decoration:none;padding:6px 13px;letter-spacing:.3px}
.main-nav a.active{background:var(--teal);color:var(--white);border-radius:12px;padding:7px 16px}
.hero{position:absolute;left:0;top:62px;width:742px;height:310px;
  background:radial-gradient(circle at 70% 45%,#e8741a 0%,#c9561a 22%,transparent 45%),
  radial-gradient(circle at 18% 30%,#d86a1c 0%,transparent 35%),
  linear-gradient(100deg,#8a9a2c 0%,#c8a22e 30%,#d9862a 55%,#b83a1c 80%,#3a1610 100%)}
.hero h1{position:absolute;left:0;right:0;top:124px;text-align:center;color:var(--white);font-size:24px;font-weight:800;line-height:29px;letter-spacing:.5px}
.hero .arrow{position:absolute;top:142px}
.welcome,.love{position:absolute;left:0;width:742px;text-align:center}
.welcome{top:372px;height:181px}
.section-title{font-size:16.5px;font-weight:800;color:var(--blue);letter-spacing:.5px}
.lead{font-size:8.6px;line-height:15.5px;color:var(--text)}
.btn{display:inline-block;border:1.5px solid var(--teal);color:var(--teal);border-radius:14px;font-size:8px;font-weight:700;padding:7px 20px;text-decoration:none;letter-spacing:.3px}
.services{position:absolute;left:0;top:553px;width:742px;height:297px;background:var(--band);text-align:center}
.services .section-title{margin-top:29px}
.services .lead{margin-top:6px}
.service{position:absolute;width:150px;height:150px;border-radius:50%;background:#e9e9e9;display:flex;align-items:center;justify-content:center}
.service .disc{width:140px;height:140px;border-radius:50%;display:flex;flex-direction:column;align-items:center;justify-content:center;color:var(--white);font-size:10.5px;font-weight:800;line-height:15.5px;letter-spacing:.4px}
.service svg{margin-bottom:14px}
.residential{left:46px;top:45px}.residential .disc{background:var(--orange)}
.investment{left:213px;top:111px}.investment .disc{background:var(--teal)}
.self-employed{left:379px;top:111px}.self-employed .disc{background:var(--red)}
.non-conforming{left:547px;top:45px}.non-conforming .disc{background:var(--blue)}
.love{top:850px;height:184px}
.site-footer{position:absolute;left:0;top:1034px;width:742px;height:166px;background:var(--dark);color:#ddd}
.footer-brand{position:absolute;left:46px;top:40px;font-size:19px;font-weight:700;color:var(--white)}
.copyright{position:absolute;left:46px;top:90px;font-size:7.8px;line-height:13.5px;color:#cfcfcf}
.footer-col{position:absolute;top:28px}
.footer-col h3{font-size:9.5px;font-weight:700;color:var(--white);letter-spacing:.4px;margin-bottom:6px}
.footer-col li{list-style:none;font-size:7.8px;line-height:17.2px;color:var(--white)}
.sitemap{left:222px}
.contact{left:379px}
.contact .org{font-size:7.6px;font-weight:700;color:var(--orange);line-height:13px}
.contact p{font-size:7.8px;line-height:12.5px;color:var(--white)}
.contact .mail{margin-top:4px;display:flex;align-items:center;gap:6px}
.connect{left:547px}
.social{display:flex;gap:9px;margin-top:10px}
.social span{width:13px;height:13px;background:#9a9a9a;border-radius:2px;display:block}
</style>
</head>
<body>
<header class="site-header">
  <div class="brand">Lark Lending</div>
  <nav class="main-nav">
    <a class="active" href="#">HOME</a>
    <a href="#">ABOUT</a>
    <a href="#">SERVICES</a>
    <a href="#">PROPERTY ADVICE</a>
    <a href="#">CONTACT</a>
  </nav>
</header>

<section class="hero" role="img" aria-label="Close-up photograph of bright orange autumn maple leaves against a blurred green and red background">
  <svg class="arrow" style="left:37px" width="14" height="26" viewBox="0 0 14 26"><path d="M12 2 L3 13 L12 24" stroke="#ffffff" stroke-opacity=".7" stroke-width="3" fill="none"/></svg>
  <h1>A FRESH START FOR YOUR FINANCE<br>WHEN OTHERS SAY NO</h1>
  <svg class="arrow" style="left:690px" width="14" height="26" viewBox="0 0 14 26"><path d="M2 2 L11 13 L2 24" stroke="#ffffff" stroke-opacity=".7" stroke-width="3" fill="none"/></svg>
</section>

<section class="welcome">
  <h2 class="section-title" style="margin-top:31px">WELCOME TO LARK LENDING</h2>
  <p class="lead" style="margin-top:10px">Marcus lives in Brookvale and loves exploring the Ridgeline Shire with his wife and kids for great places to eat.<br>With over 10 years' experience in financial services ranging from insurance, superannuation, investments and finance, Marcus<br>bringing together his experience to provide a more holistic approach to his customers.</p>
  <a class="btn" href="#" style="margin-top:18px">READ MORE</a>
</section>

<section class="services">
  <h2 class="section-title">OUR SERVICE</h2>
  <p class="lead">Vestibulum ante ipsum primis in faucibus orci luctus et ultrices posuere cubilia.</p>
  <div class="service residential"><div class="disc">
    <svg width="44" height="36" viewBox="0 0 44 36"><path d="M22 2 L2 20 L7 20 L7 34 L17 34 L17 24 L27 24 L27 34 L37 34 L37 20 L42 20 Z" fill="#fff"/></svg>
    RESIDENTIAL<br>LOANS</div></div>
  <div class="service investment"><div class="disc">
    <svg width="42" height="28" viewBox="0 0 42 28"><rect x="1" y="1" width="40" height="26" rx="2" fill="#fff"/><rect x="6" y="5" width="30" height="18" rx="1" fill="none" stroke="#00a990" stroke-width="2"/><circle cx="21" cy="14" r="7" fill="#00a990"/><text x="21" y="18" font-size="11" font-weight="800" fill="#fff" text-anchor="middle" font-family="Open Sans,sans-serif">1</text></svg>
    INVESTMENT<br>LOANS</div></div>
  <div class="service self-employed"><div class="disc">
    <svg width="40" height="36" viewBox="0 0 40 36"><path d="M14 8 V4 H26 V8" stroke="#fff" stroke-width="3" fill="none"/><rect x="1" y="8" width="38" height="27" rx="3" fill="#fff"/><rect x="8" y="8" width="3" height="27" fill="#ec1f27"/><rect x="29" y="8" width="3" height="27" fill="#ec1f27"/></svg>
    SELF EMPLOYED<br>LOANS</div></div>
  <div class="service non-conforming"><div class="disc">
    <svg width="30" height="36" viewBox="0 0 30 36"><path d="M1 1 H20 L29 10 V35 H1 Z" fill="#fff"/><path d="M20 1 V10 H29" fill="#0a8ccc"/><rect x="7" y="16" width="16" height="2.5" fill="#0a8ccc"/><rect x="7" y="22" width="16" height="2.5" fill="#0a8ccc"/><rect x="7" y="28" width="16" height="2.5" fill="#0a8ccc"/></svg>
    NON CONFIRMING<br>LOANS</div></div>
</section>

<section class="love">
  <h2 class="section-title" style="margin-top:22px">WE LOVE WHAT WE DO</h2>
  <p class="lead" style="margin-top:10px">Aliquam molestie, mi et imperdiet euismod, dui purus auctor tellus, et interdum lacus lectus et ante. Sed accumsan sollicitudin<br>sapien, sit amet adipiscing turpis gravida ac. In congue, neque ac lobortis volutpat, libero mauris varius mi,<br>vitae suscipit ipsum ligula vitae risus.</p>
  <a class="btn" href="#" style="margin-top:18px">READ MORE</a>
</section>

<footer class="site-footer">
  <div class="footer-brand">Lark Lending</div>
  <p class="copyright">Copyright © 2016. Company Name<br>All Right Reserved</p>
  <div class="footer-col sitemap">
    <h3>SITE MAP</h3>
    <ul><li>Home</li><li>About</li><li>Services</li><li>Property Advice</li><li>Contact</li></ul>
  </div>
  <div class="footer-col contact">
    <h3>CONTAC US</h3>
    <p class="org">LARK LENDING</p>
    <p>48 Wren Lane<br>Larkfield, CA 90210</p>
    <p class="mail"><svg width="9" height="7" viewBox="0 0 9 7"><rect width="9" height="7" fill="#fff"/><path d="M0 0 L4.5 4 L9 0" stroke="#444" fill="none"/></svg>marcus@larklending.example</p>
  </div>
  <div class="footer-col connect">
    <h3>CONNECT US</h3>
    <div class="social"><span></span><span></span><span></span><span></span><span></span></div>
  </div>
</footer>
</body>
</html>
```